Bulldog themed background for Real Estate Purchase Letter

I need a phantom background or watermark on a standard 8 1/2" x 11" paper. I am going to put a letter over the background. I want a bulldog theme that is cute, funny and original. This letter is for a real estate project and we want to capture the person sub-consciously . Attached is my personal dogs. If you want to use them you can but not required. I have attached the letter that I am trying to emulate. I want bulldogs not horses.

Target Market(s)

45 years old and higher

Industry/Entity Type

Real Estate

Font styles to use
Serif
Sans Serif

Colors

Designer to choose colors to be used in the design.

Requirements
Must have
• fun, happiness, reassuring,
Should not have
• violence, negativity, unhappy

```html
<!DOCTYPE html>
<html lang="en">
<head>
<meta charset="utf-8">
<title>Purchase Letter – Bulldog Letterhead</title>
<link rel="stylesheet" href="https://fonts.googleapis.com/css2?family=Montserrat:wght@500;600&family=Open+Sans:wght@400;600&display=swap">
<style>
  :root {
    --blue-deep: #0a3cb4;
    --blue-mid: #0d6fd8;
    --cyan: #19a9ec;
    --paper: #ffffff;
    --ink: #474747;
    --ink-strong: #3a3a3a;
    --dog-warm: #c9b9a6;
    --dog-light: #ece6df;
  }
  html, body { margin: 0; padding: 0; overflow: hidden; background: var(--paper); }
  .letter {
    position: relative;
    width: 850px; height: 1200px;
    overflow: hidden;
    background: var(--paper);
    font-family: "Open Sans", Arial, sans-serif;
    color: var(--ink);
    font-size: 17.5px;
  }
  .letter svg.waves { position: absolute; inset: 0; width: 850px; height: 1200px; }
  .bulldog-photo {
    position: absolute;
    left: 95px; top: 225px;
    width: 600px; height: 975px;
    border-radius: 46% 46% 30% 30% / 30% 30% 20% 20%;
    background: radial-gradient(ellipse at 50% 30%, var(--dog-light) 0%, var(--dog-warm) 55%, rgba(201,185,166,0) 78%);
    opacity: 0.45;
  }
  .agent-id {
    position: absolute; left: 67px; top: 48px;
    font-family: "Montserrat", Arial, sans-serif;
    font-weight: 500; font-size: 17px; line-height: 24px;
    color: #fff;
  }
  .block { position: absolute; left: 69px; width: 711px; margin: 0; }
  .recipient { top: 198px; line-height: 30.5px; }
  .recipient strong, .signature { font-weight: 600; color: var(--ink-strong); }
  .salutation { top: 330px; line-height: 30px; }
  .body-text { line-height: 33px; text-align: justify; text-indent: 40px; }
  .body-text strong { font-weight: 600; color: var(--ink-strong); }
  .p1 { top: 399px; }
  .p2 { top: 566px; }
  .p3 { top: 786px; }
  .closing { top: 1027px; line-height: 30px; }
  .signature { top: 1100px; line-height: 30px; }
</style>
</head>
<body>
<main class="letter">
  <div class="bulldog-photo" role="img" aria-label="Faded photo of a sitting bulldog as a soft background watermark"></div>

  <svg class="waves" viewBox="0 0 850 1200" aria-hidden="true">
    <defs>
      <linearGradient id="headerBlue" x1="0" y1="0" x2="1" y2="1">
        <stop offset="0" stop-color="var(--blue-deep)"/>
        <stop offset="1" stop-color="var(--blue-mid)"/>
      </linearGradient>
      <linearGradient id="footerBlue" x1="0" y1="0" x2="1" y2="1">
        <stop offset="0" stop-color="var(--blue-mid)"/>
        <stop offset="1" stop-color="var(--blue-deep)"/>
      </linearGradient>
    </defs>
    <!-- header wave -->
    <path fill="var(--cyan)" d="M0,0 H560 C480,30 420,70 360,100 C260,150 130,130 50,180 C25,195 8,215 0,240 Z"/>
    <path fill="url(#headerBlue)" d="M0,0 H540 C470,22 405,62 340,92 C240,135 120,115 42,160 C20,173 6,195 0,225 Z"/>
    <!-- footer wave -->
    <path fill="var(--cyan)" d="M850,930 C790,990 720,1040 640,1050 C520,1065 420,1060 330,1110 C280,1140 240,1170 215,1200 H850 Z"/>
    <path fill="url(#footerBlue)" d="M850,955 C800,1005 735,1055 655,1068 C530,1085 440,1085 350,1130 C305,1153 270,1177 245,1200 H850 Z"/>
  </svg>

  <div class="agent-id">Real Estate Agent ID :<br>#0247815390</div>

  <p class="block recipient"><strong>Mr. Jordan Ellery</strong><br>4820 Maple Lane<br>Brookfield FL 3471-2280</p>

  <p class="block salutation">Dear <strong>First Name</strong></p>

  <p class="block body-text p1">I am writing you, because I am interested in purchasing your property located at <strong>4820 Maple Lane Brookfield FL 3471-2280</strong> I live nearby in Larkfield and I puschages properties throught the state of PA Currently I am working on projects in the neighbourhood, which is how I learned of your property.</p>

  <p class="block body-text p2">Please call me at <strong>(XXX) XXXX-Local#</strong> so I can tell you how we can buy your property quickly, with no hassels and most importantly, at a fair price. I purchase the hous directly from you so there are no real estate commissions or extra fees coming out of your pocket. Furthermore, I always make cash offers so you never have to worry about delays resulting from a buyer trying to qualify for a mortgage and wasting your valuable time.</p>

  <p class="block body-text p3">I'will be glade to personally tell you more about how we can work together. All call are completely confidential and there is no obligation whatsoever. Even if you are not intersted in selling at thing time call <strong>(xxx) xxxx-xxxx</strong>, so I can help you with determining the value of your property. You should also keep this letter for your future reference, since things in life have a tendency to change unexpectedly. Thanks you for your time and consideration and I look forward to speaking with you.</p>

  <p class="block closing">Sincerely,</p>

  <p class="block signature">Dana Whitfield</p>
</main>
</body>
</html>
```